PHGCCUL re-branding website and logo

We are looking for a new webpage design and logo our current page address is www.phgccul-example.org. We want to create a new design using PHGCCUL Pinewood and Harbour Growers Co-operative Credit Union limited and another with the purposed new name PHFC Pinewood and Harbour Financial Co-operative, the color scheme is purple and burnt orange. Our new logo and webpage should communicate change and growth purposed theme continuing our legacy here to server past, present and future generations. Our idea for the logo is a live shot of hands of different ages in a circle holding a tree

Target Market(s)

Everyone

Contact Information for Business Card

Company Name
Telephone number
Address
slot to enter employee info

Logo Text

(P & H) Pinewood And Harbour Financial Co-operative

Coding

Coded - Design and coding required

Number of Pages Required

2 page

Colors
f37122
fbed22
6b449b

Requirements
Must have
• links for social media

```html
<!DOCTYPE html>
<html lang="en">
<head>
<meta charset="utf-8">
<title>Pinewood &amp; Harbour Financial Co-operative</title>
<link href="https://fonts.googleapis.com/css2?family=Open+Sans:wght@400;600&family=Roboto:wght@400;500&family=Roboto+Condensed:wght@400;700&display=swap" rel="stylesheet">
<style>
:root{
  --orange:#f37122;
  --purple:#6b449b;
  --black:#000;
  --ink:#333;
  --muted:#666;
  --light:#f3f3f4;
  --footer:#1c1c1c;
  --white:#fff;
}
*{box-sizing:border-box;margin:0;padding:0}
h1,h2,h3,h4,h5{font-weight:400}
html,body{width:1200px;height:2936px;overflow:hidden}
body{font-family:"Open Sans",sans-serif;color:var(--ink);background:var(--white);position:relative}
a{color:inherit;text-decoration:none}

/* header */
.site-header{position:absolute;left:0;top:0;width:1200px;height:135px;background:var(--black);color:var(--white)}
.brand{position:absolute;left:100px;top:24px;display:flex;align-items:center;gap:14px}
.brand-circle{width:60px;height:60px;border-radius:50%;background:var(--orange)}
.brand-name{font-family:"Open Sans",sans-serif;font-weight:400;font-size:18px;line-height:24px;color:var(--white)}
.call{position:absolute;left:750px;top:32px;font-family:"Roboto",sans-serif;font-size:16px;font-weight:500;letter-spacing:.5px}
.teller-btn{position:absolute;left:934px;top:27px;width:167px;height:34px;background:var(--orange);font-family:"Roboto Condensed",sans-serif;font-size:13px;line-height:34px;text-align:center;text-transform:uppercase}
.main-nav{position:absolute;right:98px;top:86px;display:flex;gap:27px;font-family:"Roboto Condensed",sans-serif;font-size:12px;text-transform:uppercase}
.main-nav .active{color:var(--orange)}

/* hero */
.hero{position:absolute;left:0;top:135px;width:1200px;height:490px;background:radial-gradient(ellipse at 75% 55%,#e8d6c2 0%,#d7d2c6 35%,#c6d1cf 70%,#b8c6c5 100%)}
.hero-title{position:absolute;left:98px;top:168px;font-family:"Roboto Condensed",sans-serif;font-weight:700;font-size:39px;line-height:48px;color:#333;text-transform:uppercase}
.hero-btn{position:absolute;left:98px;top:279px;width:117px;height:36px;background:var(--orange);color:var(--white);font-family:"Roboto Condensed",sans-serif;font-size:15px;line-height:36px;text-align:center}
.slide-arrow{position:absolute;width:34px;height:34px;border-radius:50%;background:rgba(0,0,0,.25);display:flex;align-items:center;justify-content:center}

/* welcome */
.welcome-title{position:absolute;left:0;top:680px;width:1200px;text-align:center;font-family:"Roboto",sans-serif;font-weight:400;font-size:36px;color:#333}
.welcome-text{position:absolute;left:125px;top:742px;width:950px;text-align:center;font-size:10.5px;line-height:19px;color:#555}
.feature-card{position:absolute;top:848px;width:280px;height:168px;color:var(--white);padding:22px 14px 0 56px}
.feature-card.orange{background:var(--orange)}
.feature-card.purple{background:var(--purple)}
.feature-card h3{font-family:"Roboto",sans-serif;font-weight:400;font-size:16px;text-transform:uppercase;margin-bottom:8px;white-space:nowrap}
.feature-card p{font-size:11px;line-height:19px}
.feature-card .more{display:block;margin-top:12px;font-family:"Roboto Condensed",sans-serif;font-size:12px}
.feature-icon{position:absolute;top:40px;left:-42px;width:84px;height:84px;border-radius:50%;border:4px solid var(--white);display:flex;align-items:center;justify-content:center}
.orange .feature-icon{background:var(--orange)}
.purple .feature-icon{background:var(--purple)}

/* tools */
.tools{position:absolute;left:0;top:1105px;width:1200px;height:485px;background:var(--light)}
.tools-image{position:absolute;left:140px;top:65px;width:355px;height:340px;background:linear-gradient(160deg,#d9d9d9 0%,#b9b4ad 55%,#8c8c8c 100%);border-radius:6px}
.tools-title{position:absolute;left:592px;top:70px;font-family:"Roboto",sans-serif;font-weight:400;font-size:28px;color:var(--purple);text-transform:uppercase}
.tool{position:absolute;width:240px}
.tool-icon{width:58px;height:54px;background:var(--purple);display:flex;align-items:center;justify-content:center;margin-bottom:18px}
.tool h4{font-family:"Roboto",sans-serif;font-weight:400;font-size:13.5px;text-transform:uppercase;color:#333;margin-bottom:4px}
.tool p{font-size:11px;line-height:17px;color:#555}

/* products */
.section-title{position:absolute;left:0;width:1200px;text-align:center;font-family:"Roboto",sans-serif;font-weight:400;font-size:29px;color:#333;text-transform:uppercase}
.title-rule{position:absolute;left:576px;top:1694px;width:48px;height:3px;background:var(--orange)}
.product{position:absolute;top:1737px;width:312px}
.product-image{width:312px;height:175px;border:2px solid #ddd}
.product h3{font-family:"Roboto",sans-serif;font-weight:400;font-size:20px;color:#333;margin:16px 0 6px}
.product p{font-size:11px;line-height:20px;color:#666}
.outline-btn{display:inline-block;margin-top:14px;border:1px solid #999;padding:4px 8px;font-size:10px;font-weight:600;color:#555}
.ring-arrow{position:absolute;top:1855px;width:26px;height:26px;border:1px solid #bbb;border-radius:50%;display:flex;align-items:center;justify-content:center}

/* news */
.news{position:absolute;left:0;top:2125px;width:1200px;height:443px;background:var(--light)}
.news-title,.rates-title{position:absolute;top:65px;font-family:"Roboto",sans-serif;font-weight:400;font-size:26px;color:#333;text-transform:uppercase}
.news-title{left:98px}
.rates-title{left:775px}
.news-item{position:absolute;top:142px;width:300px}
.news-item h4{font-family:"Roboto",sans-serif;font-weight:400;font-size:17px;color:#333}
.news-item .date{font-family:"Roboto",sans-serif;font-size:15px;color:var(--orange);margin:8px 0 8px}
.news-item p{font-size:11px;line-height:21px;color:#555}
.news-item .more{display:flex;align-items:center;gap:6px;margin-top:16px;font-size:11px;color:#555}
.rates{position:absolute;left:775px;top:120px;width:320px;background:var(--orange);color:var(--white);padding:4px 22px}
.rate-row{display:flex;justify-content:space-between;align-items:center;height:54px;border-bottom:1px solid rgba(255,255,255,.35)}
.rate-row:last-child{border-bottom:0}
.rate-row .label{font-size:12px;font-weight:600;line-height:16px}
.rate-row .value{font-family:"Roboto",sans-serif;font-size:15px;font-weight:500}
.rate-row .value small{font-size:9px}
.rates-note{position:absolute;left:777px;top:362px;font-size:10px;color:#333}
.rates-note span{text-decoration:underline;margin-left:6px}

/* footer */
.site-footer{position:absolute;left:0;top:2568px;width:1200px;height:368px;background:var(--footer);color:#ddd}
.footer-col{position:absolute;top:58px}
.footer-col h5{font-family:"Roboto",sans-serif;font-weight:400;font-size:17px;color:var(--white);text-transform:uppercase;margin-bottom:22px}
.contact-line{display:flex;gap:14px;font-size:12px;line-height:19px;margin-bottom:14px}
.contact-line svg{flex:none;margin-top:2px}
.signup p{font-size:11px;line-height:18px;width:300px}
.email-field{margin-top:16px;width:284px;height:40px;background:var(--white);color:#777;font-size:11px;padding:12px 14px}
.subscribe{margin-top:14px;width:108px;height:38px;background:var(--orange);color:var(--white);font-size:12px;line-height:38px;text-align:center}
.quick-links li{list-style:none;font-size:11px;line-height:22px;display:flex;align-items:center;gap:8px}
.quick-links li::before{content:"";border-left:5px solid #ddd;border-top:4px solid transparent;border-bottom:4px solid transparent}
.social li{list-style:none;display:flex;align-items:center;gap:10px;font-size:14px;margin-bottom:13px}
.social .ring{width:24px;height:24px;border:2px solid #ddd;border-radius:50%}
.footer-rule{position:absolute;left:0;top:290px;width:1200px;height:1px;background:#333}
.copyright{position:absolute;left:0;top:318px;width:1200px;text-align:center;font-size:11px;color:#ddd}
</style>
</head>
<body>

<header class="site-header">
  <div class="brand"><div class="brand-circle"></div><span class="brand-name">Pinewood &amp; Harbour<br>Financial Co-operative</span></div>
  <div class="call">CALL (555) 318-4470</div>
  <a class="teller-btn">Internet Teller Login</a>
  <nav class="main-nav">
    <a class="active">Home</a><a>Apply for a loan</a><a>Become a member</a><a>Products &amp; Services</a><a>My credit union</a><a>Contact</a>
  </nav>
</header>

<section class="hero" role="img" aria-label="Hands cupping a pile of coins with young green plants growing from it">
  <h1 class="hero-title">Pinewood and<br>Harbour Financial</h1>
  <a class="hero-btn">READ MORE</a>
  <div class="slide-arrow" style="left:32px;top:228px"><svg width="12" height="14" viewBox="0 0 12 14"><path d="M9 1 3 7l6 6" stroke="#fff" stroke-width="2" fill="none"/></svg></div>
  <div class="slide-arrow" style="left:1128px;top:228px"><svg width="12" height="14" viewBox="0 0 12 14"><path d="m3 1 6 6-6 6" stroke="#fff" stroke-width="2" fill="none"/></svg></div>
</section>

<h2 class="welcome-title">Welcome To Pinewood &amp; Harbour Growers</h2>
<p class="welcome-text">Sed ut perspiciatis unde omnis iste natus error sit voluptatem accusantium doloremque laudantium, totam rem aperiam, eaque ipsa quae ab illo inventore veritatis et quasi architecto beatae vitae dicta sunt explicabo. Nemo enim ipsam voluptatem quia voluptas sit aspernatur aut odit aut fugit, sed quia consequuntur magni dolores eos qui ratione voluptatem sequi nesciunt. Neque porro quisquam est, qui dolorem ipsum quia dolor sit amet, consectetur, adipisci velit, sed quia non numquam</p>

<div class="feature-card orange" style="left:135px">
  <div class="feature-icon"><svg width="36" height="40" viewBox="0 0 36 40" fill="none" stroke="#fff" stroke-width="2.5"><path d="M4 3h20l8 8v26H4z"/><path d="M10 16h14M10 22h14M10 28h9"/></svg></div>
  <h3>Apply for a loan</h3>
  <p>Lorem ipsum dolor sit amet, sectetur adipiscing elit, sed do eiusmod tempor incididunt ut labore et dolore</p>
  <a class="more">READ MORE ❯</a>
</div>
<div class="feature-card purple" style="left:478px">
  <div class="feature-icon"><svg width="34" height="36" viewBox="0 0 34 36" fill="#fff"><circle cx="17" cy="10" r="8"/><path d="M2 35c0-9 7-15 15-15s15 6 15 15z"/></svg></div>
  <h3>Become a member</h3>
  <p>Lorem ipsum dolor sit amet, sectetur adipiscing elit, sed do eiusmod tempor incididunt ut labore et dolore</p>
  <a class="more">READ MORE ❯</a>
</div>
<div class="feature-card orange" style="left:823px">
  <div class="feature-icon"><svg width="38" height="40" viewBox="0 0 38 40" fill="none" stroke="#fff" stroke-width="2.5"><rect x="3" y="3" width="22" height="32"/><path d="M8 9h12M8 16h3M14 16h3M8 22h3M14 22h3M8 28h3"/><circle cx="28" cy="28" r="8"/></svg></div>
  <h3>Financial Calculators</h3>
  <p>Lorem ipsum dolor sit amet, sectetur adipiscing elit, sed do eiusmod tempor incididunt ut labore et dolore</p>
  <a class="more">READ MORE ❯</a>
</div>

<section class="tools">
  <div class="tools-image" role="img" aria-label="Desktop monitor showing staff meeting with members in an office"></div>
  <h2 class="tools-title">Tools &amp; Benefits</h2>
  <div class="tool" style="left:596px;top:137px">
    <div class="tool-icon"><svg width="28" height="30" viewBox="0 0 28 30" fill="none" stroke="#fff" stroke-width="2"><path d="M3 3h16v24H3z"/><path d="M7 10h8M7 15h8M7 20h5M24 6 14 20l-1 4 4-2L27 8z"/></svg></div>
    <h4>Online Loan Application</h4>
    <p>Lorem ipsum dolor sit amet, consectetur adipiscing elit, sed do eiusmod</p>
  </div>
  <div class="tool" style="left:870px;top:137px">
    <div class="tool-icon"><svg width="24" height="30" viewBox="0 0 24 30" fill="#fff"><path d="M6 13V8a6 6 0 0 1 12 0v1h-3V8a3 3 0 0 0-6 0v5z"/><rect x="2" y="13" width="20" height="15"/></svg></div>
    <h4>Internet Teller Sign Up Form</h4>
    <p>Lorem ipsum dolor sit amet, consectetur adipiscing elit, sed do eiusmod</p>
  </div>
  <div class="tool" style="left:596px;top:291px">
    <div class="tool-icon"><svg width="26" height="28" viewBox="0 0 26 28" fill="#fff"><circle cx="13" cy="8" r="6"/><path d="M1 27c0-7 5-12 12-12s12 5 12 12z"/></svg></div>
    <h4>Member Services Benefits</h4>
    <p>Lorem ipsum dolor sit amet, consectetur adipiscing elit, sed do eiusmod</p>
  </div>
  <div class="tool" style="left:870px;top:291px">
    <div class="tool-icon"><svg width="28" height="28" viewBox="0 0 28 28" fill="none" stroke="#fff" stroke-width="2"><rect x="2" y="5" width="24" height="21"/><path d="M2 11h24M8 2v6M20 2v6M7 16h3M13 16h3M19 16h3M7 21h3M13 21h3"/></svg></div>
    <h4>Financial Calculators</h4>
    <p>Lorem ipsum dolor sit amet, consectetur adipiscing elit, sed do eiusmod</p>
  </div>
</section>

<h2 class="section-title" style="top:1648px">Products &amp; Services</h2>
<div class="title-rule"></div>
<div class="ring-arrow" style="left:47px"><svg width="8" height="10" viewBox="0 0 8 10"><path d="M6 1 2 5l4 4" stroke="#aaa" stroke-width="1.5" fill="none"/></svg></div>
<div class="ring-arrow" style="left:1127px"><svg width="8" height="10" viewBox="0 0 8 10"><path d="m2 1 4 4-4 4" stroke="#aaa" stroke-width="1.5" fill="none"/></svg></div>
<article class="product" style="left:98px">
  <div class="product-image" role="img" aria-label="Advisors in suits discussing a loan with clients" style="background:linear-gradient(135deg,#c9ced4,#7f8a96)"></div>
  <h3>Consumer Loans</h3>
  <p>Sed ut perspiciatis unde omnis iste natus error sit voluptatem accusantium doloremque laudantium, totam</p>
  <a class="outline-btn">READ MORE ➜</a>
</article>
<article class="product" style="left:443px">
  <div class="product-image" role="img" aria-label="Service agent wearing a headset taking a call" style="background:linear-gradient(135deg,#f2f2f2,#c9b7a8)"></div>
  <h3>Loans By Phone</h3>
  <p>Sed ut perspiciatis unde omnis iste natus error sit voluptatem accusantium doloremque laudantium, totam</p>
  <a class="outline-btn">READ MORE ➜</a>
</article>
<article class="product" style="left:787px">
  <div class="product-image" role="img" aria-label="Two golfers on a green course on vacation" style="background:linear-gradient(180deg,#4f8a2c,#79a83f)"></div>
  <h3>Vacation Club</h3>
  <p>Sed ut perspiciatis unde omnis iste natus error sit voluptatem accusantium doloremque laudantium, totam</p>
  <a class="outline-btn">READ MORE ➜</a>
</article>

<section class="news">
  <h2 class="news-title">News &amp; Events</h2>
  <article class="news-item" style="left:96px">
    <h4>Nemo Enim Ipsam Voluptatem ?</h4>
    <div class="date">Janu 21, 2017</div>
    <p>Duis aute irure dolor in reprehenderit in voluptate velit esse cillum dolore eu fugiat nulla pariatur. Excepteur sint occaecat cupidatat non proident, sunt in culpa qui officia deserunt mollit</p>
    <a class="more"><svg width="11" height="11" viewBox="0 0 11 11"><circle cx="5.5" cy="5.5" r="5" fill="#555"/><path d="m4 3 3 2.5L4 8" stroke="#fff" fill="none"/></svg>READ MORE</a>
  </article>
  <article class="news-item" style="left:447px">
    <h4>Nemo Enim Ipsam Voluptatem ?</h4>
    <div class="date">Janu 21, 2017</div>
    <p>Duis aute irure dolor in reprehenderit in voluptate velit esse cillum dolore eu fugiat nulla pariatur. Excepteur sint occaecat cupidatat non proident, sunt in culpa qui officia deserunt mollit</p>
    <a class="more"><svg width="11" height="11" viewBox="0 0 11 11"><circle cx="5.5" cy="5.5" r="5" fill="#555"/><path d="m4 3 3 2.5L4 8" stroke="#fff" fill="none"/></svg>READ MORE</a>
  </article>
  <h2 class="rates-title">Featured Rates</h2>
  <div class="rates">
    <div class="rate-row"><span class="label">Consumer Loans<br>as low as</span><span class="value">9.00% <small>APR*</small></span></div>
    <div class="rate-row"><span class="label">New Auto/Motorcycle<br>as low as</span><span class="value">7.00% <small>APR*</small></span></div>
    <div class="rate-row"><span class="label">Used Auto/Motorcycle<br>as low as</span><span class="value">11.75% <small>APR*</small></span></div>
    <div class="rate-row"><span class="label">Mortgages<br>as low as</span><span class="value">8.25% <small>APR*</small></span></div>
  </div>
  <p class="rates-note">*APR - Annual Percentage Rate. <span>APPLY FOR A LOAN &gt;</span></p>
</section>

<footer class="site-footer">
  <div class="footer-col" style="left:98px">
    <h5>Contact Us</h5>
    <div class="contact-line"><svg width="14" height="18" viewBox="0 0 14 18" fill="none" stroke="#ddd" stroke-width="1.5"><path d="M7 17s6-6 6-10A6 6 0 0 0 1 7c0 4 6 10 6 10z"/><circle cx="7" cy="7" r="2"/></svg><span>Location: Harbour Road &amp;<br>Pinewood Ave.</span></div>
    <div class="contact-line"><svg width="16" height="16" viewBox="0 0 16 16" fill="none" stroke="#ddd" stroke-width="1.5"><path d="M3 1h3l1.5 4-2 1.5a9 9 0 0 0 4 4l1.5-2 4 1.5v3a1.5 1.5 0 0 1-1.5 1.5A13 13 0 0 1 1.5 2.5 1.5 1.5 0 0 1 3 1z"/></svg><span>Phone : (555) 318-4470</span></div>
    <div class="contact-line"><svg width="16" height="12" viewBox="0 0 16 12" fill="none" stroke="#ddd" stroke-width="1.5"><rect x="1" y="1" width="14" height="10"/><path d="m1 1 7 6 7-6"/></svg><span>E-mail : info@phgccul-example.org</span></div>
  </div>
  <div class="footer-col signup" style="left:405px">
    <h5>Sign up to receive email</h5>
    <p>Excepteur sint occaecat cupidatat non proident, sunt in culpa qui Nemo enim ipsam voluptatem</p>
    <div class="email-field">Enter Email</div>
    <div class="subscribe">SUBSCRIBE</div>
  </div>
  <div class="footer-col" style="left:772px">
    <h5>Quick Links</h5>
    <ul class="quick-links">
      <li>Home</li><li>Apply For A Loan</li><li>Become A Member</li><li>My credit union</li><li>Products &amp; Services</li><li>Tools &amp; Benefits</li><li>Contact Us</li>
    </ul>
  </div>
  <div class="footer-col" style="left:976px">
    <h5>Social Media</h5>
    <ul class="social">
      <li><span class="ring"></span>FriendSpace</li>
      <li><span class="ring"></span>Chirper</li>
      <li><span class="ring"></span>CirclePlus</li>
      <li><span class="ring"></span>ViewTube</li>
    </ul>
  </div>
  <div class="footer-rule"></div>
  <p class="copyright">Copyright © Pinewood &amp; Harbour Growers Co-operative Credit Union Ltd 2016. All rights reserved.</p>
</footer>

</body>
</html>
```